Real Estate Brokerage Stationery Designs

I am looking to have presentation folders with business card slots on both sides along with pockets on both sides. I've attached logos, website colors along with current business card designs.

I am looking for envelope designs both big and small. Possibly new business card designs, notepad templates for big and small notepads. Letterhead designs. Pop socket designs. Realtors name badge designs.

www.brightholdrealty.example

```html
<!DOCTYPE html>
<html lang="en">
<head>
<meta charset="utf-8">
<title>Brighthold Realty – Notebook Cover</title>
<link rel="stylesheet" href="https://fonts.googleapis.com/css2?family=Open+Sans:wght@700&display=swap">
<style>
  :root {
    --backdrop: #c4c4c4;
    --spine: #5b87d4;
    --sky-top: #80bfff;
    --sky-mid: #4a8fdc;
    --sky-bottom: #1e66bb;
    --silver-light: #f4f6f8;
    --silver-dark: #aab3bd;
    --haze: #a9bde3;
    --brand-blue: #1f5bb6;
    --strip: #f1f3f5;
    --ink: #1b1b1b;
    --link-blue: #1e4f9f;
  }
  html, body {
    margin: 0;
    width: 1157px;
    height: 1200px;
    overflow: hidden;
    background: var(--backdrop);
  }
  .notebook-cover {
    position: absolute;
    left: 245px;
    top: 48px;
    width: 673px;
    height: 1044px;
  }
  .notebook-cover svg { display: block; width: 100%; height: 100%; }
  .brand-name {
    font-family: "Open Sans", sans-serif;
    font-weight: 700;
    font-size: 60px;
    fill: var(--ink);
  }
  .web-address {
    font-family: "Open Sans", sans-serif;
    font-weight: 700;
    font-size: 25px;
    fill: var(--link-blue);
  }
</style>
</head>
<body>
<main class="notebook-cover">
  <svg viewBox="0 0 841 1305" xmlns="http://www.w3.org/2000/svg">
    <defs>
      <linearGradient id="sky" x1="0" y1="0" x2="0" y2="1">
        <stop offset="0" stop-color="var(--sky-top)"/>
        <stop offset="0.5" stop-color="var(--sky-mid)"/>
        <stop offset="1" stop-color="var(--sky-bottom)"/>
      </linearGradient>
      <linearGradient id="silver" x1="0" y1="1" x2="1" y2="0">
        <stop offset="0" stop-color="var(--silver-dark)"/>
        <stop offset="0.45" stop-color="var(--silver-light)"/>
        <stop offset="0.75" stop-color="var(--silver-dark)"/>
        <stop offset="1" stop-color="var(--haze)"/>
      </linearGradient>
      <linearGradient id="photo" x1="0" y1="0" x2="0" y2="1">
        <stop offset="0" stop-color="#9fb4de"/>
        <stop offset="0.25" stop-color="#cbbfb4"/>
        <stop offset="0.45" stop-color="#e3c89c"/>
        <stop offset="0.62" stop-color="#b79a78"/>
        <stop offset="0.74" stop-color="#56703f"/>
        <stop offset="0.82" stop-color="#a08890"/>
        <stop offset="1" stop-color="#c7aeb6"/>
      </linearGradient>
    </defs>

    <rect class="spine" x="0" y="0" width="40" height="1305" fill="var(--spine)"/>

    <path class="cover-background" fill="url(#sky)"
      d="M33,0 H801 Q841,0 841,40 V1305 H33 Z"/>

    <path class="silver-wave" fill="url(#silver)"
      d="M33,1170 C150,950 280,840 500,800 C700,765 805,610 841,450 L841,1255 L33,1255 Z"/>

    <path class="home-photo" role="img" aria-label="Photo of a lit two-storey suburban home at dusk with a garden and paved driveway"
      fill="url(#photo)"
      d="M33,1195 C160,965 300,865 560,838 C700,822 790,770 841,722 L841,1255 L33,1255 Z"/>

    <rect class="brand-mark" x="383" y="150" width="160" height="160" fill="var(--brand-blue)"/>
    <text class="brand-name" x="463" y="500" text-anchor="middle">Brighthold Realty</text>

    <path class="footer-strip" fill="var(--strip)"
      d="M33,1255 H841 V1265 Q841,1305 801,1305 H33 Z"/>
    <text class="web-address" x="438" y="1289" text-anchor="middle">www.brightholdrealty.example</text>
  </svg>
</main>
</body>
</html>
```